EB-5 Regional Center needs a Web design

Harlow Ridge Financial Partners is an expanding EB-r regional center. We have been successful in sponsoring multiple projects of third-party developers and placing EB-5, B-1, and Private Investments into multiple projects.

We are now partnering directly with project developers in the energy and healthcare to raise foreign capital for projects in those industries. The foreign capital is used as project equity and our collective balance sheets are used to guarantee debt to complete the funding of the projects.

We need a web site where we can post our company credentials, the bios of each partner, a document page for each of our projects where we can post specific project related documents which foreign investors can read, and we will need a section where foreign investors can fill out investor forms confirming that they are qualified investors and leaving their contact so that our agents and executives can make contact.

The final design should reflect the exceptional experience of the partners and our financial strength and stability.

We do have a logo we would want to use on the web design.

Target Market(s)

EB-5 Investors, B-1 Investors, Private Equity and other investors seeking quality investment in job creating US projects.

Coding

Number of Pages Required

5+ page

Font styles to use
Sans Serif

Requirements
Must have
• Pages to display company info, partner bios, projects completed, and a projects in-process page where we can post documents and info on projects for which we are seeking foreign investment. We also need a section where investors can enter their qualifying personal information and leave contact information for us.

```html
<!DOCTYPE html>
<html lang="en">
<head>
<meta charset="utf-8">
<title>Harlow Ridge Financial Partners</title>
<link rel="stylesheet" href="https://fonts.googleapis.com/css2?family=Montserrat:wght@400;500;600&family=Tinos:wght@400&display=swap">
<style>
:root{
  --navy:#0b2a66;
  --grey-light:#a9a9ac;
  --grey-mid:#8b8b8e;
  --grey-text:#7d7d80;
  --ink:#1a1a1a;
  --body:#444;
  --white:#fff;
  --paper:#f3f3f3;
}
*{margin:0;padding:0;box-sizing:border-box}
html,body{width:1200px;height:3681px;overflow:hidden;background:var(--white)}
body{position:relative;font-family:'Montserrat',sans-serif;color:var(--ink)}
.abs{position:absolute}
a{color:inherit;text-decoration:none}

/* header */
.site-header{position:absolute;left:0;top:0;width:1200px;height:79px;background:var(--white);z-index:5}
.brand{position:absolute;left:90px;top:12px;display:flex;align-items:center;gap:12px;color:#77777a;font-weight:500}
.brand-mark{width:44px;height:44px;border-radius:50%;background:#8d8d90}
.brand-name{font-size:31px;line-height:1;letter-spacing:.5px;text-transform:uppercase;white-space:nowrap}
.brand-sub{font-size:13px;letter-spacing:3px;margin-top:3px;white-space:nowrap}
.main-nav{position:absolute;top:32px;left:457px;font-size:16px;color:#444}
.main-nav a{position:absolute;white-space:nowrap}
.main-nav .active{color:var(--navy)}
.cta-tab{position:absolute;left:883px;top:0;width:227px;height:107px;z-index:6}
.cta-tab span{position:absolute;left:0;top:30px;width:227px;text-align:center;color:var(--white);font-weight:600;font-size:17px}

/* hero */
.hero{position:absolute;left:0;top:79px;width:1200px;height:590px;
  background:linear-gradient(115deg,#6f86b3 0%,#9fb0c9 30%,#c9ced6 55%,#aab2bf 80%,#7d8697 100%)}
.hero-title{position:absolute;left:0;top:140px;width:1200px;text-align:center;color:var(--white);font-weight:600;font-size:74px;letter-spacing:2px;white-space:nowrap}
.hero-sub{position:absolute;left:0;top:240px;width:1200px;text-align:center;color:var(--white);font-family:'Tinos',serif;font-size:28px;letter-spacing:8px}
.btn{display:inline-block;font-weight:600;color:var(--white);background:var(--navy);text-align:center}
.hero-btn{position:absolute;left:501px;top:320px;width:196px;height:52px;line-height:52px;font-size:18px}
.arrow{position:absolute;top:275px}

/* services */
.services{position:absolute;left:0;top:579px;width:1200px;height:460px}
.service{position:absolute;top:120px;width:400px;text-align:center;color:var(--white)}
.service h3{font-weight:500;font-size:27px;margin-top:20px}
.service p{font-size:15.5px;line-height:30px;margin-top:14px;color:#f0f0f0;padding:0 40px}

/* welcome */
.welcome-bg{position:absolute;left:0;top:1293px;width:400px;height:388px;background:var(--paper)}
.welcome-frame{position:absolute;left:99px;top:1133px;width:510px;height:446px;background:var(--navy)}
.welcome-img{position:absolute;left:90px;top:1143px;width:510px;height:443px;
  background:linear-gradient(135deg,#b49a97 0%,#d9d7da 40%,#e8e9ec 70%,#c9cbd0 100%)}
.welcome-text{position:absolute;left:654px;top:1150px;width:460px}
.section-title{font-weight:500;font-size:35px;line-height:33px}
.section-title .muted{color:var(--grey-text)}
.rule{width:32px;height:5px;background:var(--navy);margin-top:18px}
.serif-copy{font-family:'Tinos',serif;font-size:16.5px;line-height:32.3px;color:var(--body);text-align:justify;margin-top:22px}
.welcome-btn{position:absolute;left:654px;top:1526px;width:153px;height:48px;line-height:48px;font-size:16px}

/* feature band */
.band{position:absolute;top:1681px;height:557px}
.band-left{left:0;width:601px;background:linear-gradient(160deg,#2b467f,#1c3872 60%,#304b84);clip-path:polygon(0 0,100% 33px,100% 530px,0 100%)}
.band-right{left:601px;width:599px;background:linear-gradient(200deg,#3f3f44,#66666a 50%,#4d4d52);clip-path:polygon(0 33px,100% 0,100% 100%,0 530px)}
.band-block{position:absolute;top:1800px;width:480px;color:var(--white)}
.band-block h2{font-weight:500;font-size:33px;line-height:44px;white-space:nowrap}
.band-block .rule{background:var(--white);margin-top:20px}
.band-block p{width:425px;font-size:15.5px;line-height:29.5px;margin-top:26px}
.band-right-block p{text-align:justify}
.band-btn{position:absolute;top:2071px;width:153px;height:49px;line-height:49px;font-size:16px}

/* partners */
.partners-title{position:absolute;left:0;top:2325px;width:1200px;text-align:center;font-weight:500;font-size:36px}
.partners-rule{position:absolute;left:585px;top:2386px;width:30px;height:5px;background:var(--navy)}
.partner{position:absolute;top:2421px;width:312px;height:330px;background:var(--grey-mid);text-align:center;color:var(--white);font-family:'Tinos',serif}
.partner-photo{height:245px;background:linear-gradient(180deg,#d6d2cf,#b7aaa2 60%,#7d6a60)}
.partner h4{font-weight:400;font-size:28px;margin-top:12px}
.partner span{font-size:15px}

/* contact */
.contact-left{position:absolute;left:0;top:2826px;width:601px;height:557px;background:linear-gradient(180deg,#919194,#878789);clip-path:polygon(0 0,100% 35px,100% 524px,0 100%)}
.contact-right{position:absolute;left:601px;top:2826px;width:599px;height:557px;background:linear-gradient(200deg,#22355f,#4f6489 45%,#8d9ab3 75%,#b7c0cf);clip-path:polygon(0 35px,100% 0,100% 100%,0 524px)}
.contact-text{position:absolute;left:89px;top:2925px;width:460px;color:var(--white)}
.contact-text h2{font-weight:500;font-size:36px}
.contact-text .rule{background:var(--white)}
.contact-text .serif-copy{color:var(--white);font-size:16px;line-height:31.5px;margin-top:26px;text-align:left}
.address{font-family:'Tinos',serif;font-size:16px;line-height:31.5px;margin-top:10px}
.address small{font-size:13px}
.field{position:absolute;left:640px;width:470px;background:var(--white);font-size:15px;color:#888;padding:12px 15px}
.submit{position:absolute;left:640px;top:3219px;width:150px;height:46px;line-height:46px;font-size:16px}

/* footer */
.footer-brand{position:absolute;left:0;top:3462px;width:1200px;justify-content:center}
.footer-brand .brand-name{font-size:30px}
.footer-nav{position:absolute;left:0;top:3528px;width:1200px;text-align:center;font-size:16px;color:#444}
.footer-nav a{margin:0 13px}
.social{position:absolute;left:0;top:3572px;width:1200px;display:flex;justify-content:center;gap:9px}
.social span{width:40px;height:40px;border-radius:50%;border:2px solid var(--navy)}
.copyright{position:absolute;left:0;top:3638px;width:1200px;text-align:center;font-size:12px;color:#555}
</style>
</head>
<body>

<header class="site-header">
  <div class="brand">
    <div class="brand-mark"></div>
    <div><div class="brand-name">Harlow Ridge</div><div class="brand-sub">Financial Partners</div></div>
  </div>
  <nav class="main-nav">
    <a class="active" style="left:0">Home</a>
    <a style="left:76px">About Us</a>
    <a style="left:180px">Projects</a>
    <a style="left:273px">Blog</a>
    <a style="left:353px">En &#8964;</a>
  </nav>
</header>
<a class="cta-tab">
  <svg width="227" height="107" viewBox="0 0 227 107"><polygon points="0,0 227,0 227,104 113,95 0,104" fill="#0b2a66"/></svg>
  <span>Get Started</span>
</a>

<section class="hero" role="img" aria-label="Photo of business people reviewing charts on a tablet at a desk">
  <h1 class="hero-title">HARLOW RIDGE</h1>
  <div class="hero-sub">Financial Partners</div>
  <a class="btn hero-btn">Get Started</a>
  <svg class="arrow" style="left:78px" width="14" height="20"><polyline points="11,2 3,10 11,18" fill="none" stroke="#fff" stroke-width="3"/></svg>
  <svg class="arrow" style="left:1110px" width="14" height="20"><polyline points="3,2 11,10 3,18" fill="none" stroke="#fff" stroke-width="3"/></svg>
</section>

<section class="services">
  <svg class="abs" style="left:0;top:0" width="1200" height="460" viewBox="0 0 1200 460">
    <polygon points="0,77 399,34 399,460 0,460" fill="#a9a9ac"/>
    <polygon points="399,34 600,12 803,34 803,460 399,460" fill="#8b8b8e"/>
    <polygon points="803,34 1200,77 1200,460 803,460" fill="#a9a9ac"/>
    <polyline points="0,74 600,6 1200,74" fill="none" stroke="#0b2a66" stroke-width="8"/>
  </svg>
  <div class="service" style="left:0">
    <svg width="46" height="46" viewBox="0 0 46 46" fill="none" stroke="#fff" stroke-width="2"><polygon points="23,3 42,13 4,13"/><line x1="6" y1="17" x2="40" y2="17"/><line x1="10" y1="20" x2="10" y2="36"/><line x1="18" y1="20" x2="18" y2="36"/><line x1="28" y1="20" x2="28" y2="36"/><line x1="36" y1="20" x2="36" y2="36"/><rect x="4" y="38" width="38" height="5"/></svg>
    <h3>Consulting</h3>
    <p>Lorem ipsum dolor sit amet, consectetur adipiscing elit, sed do eiusmod tempor incididunt ut labore et dolore magna aliqua.</p>
  </div>
  <div class="service" style="left:400px">
    <svg width="50" height="50" viewBox="0 0 50 50" fill="none" stroke="#fff" stroke-width="2"><rect x="4" y="10" width="20" height="34" rx="2"/><line x1="8" y1="16" x2="20" y2="16"/><line x1="8" y1="22" x2="20" y2="22"/><line x1="8" y1="28" x2="20" y2="28"/><circle cx="34" cy="32" r="11"/><path d="M37 27h-5a2.5 2.5 0 0 0 0 5h4a2.5 2.5 0 0 1 0 5h-5M34 24v16"/></svg>
    <h3>Financial Funds</h3>
    <p>Lorem ipsum dolor sit amet, consectetur adipiscing elit, sed do eiusmod tempor incididunt ut labore et dolore magna aliqua.</p>
  </div>
  <div class="service" style="left:803px">
    <svg width="50" height="50" viewBox="0 0 50 50" fill="none" stroke="#fff" stroke-width="2"><path d="M25 3a6 6 0 0 1 6 6c0 5-6 10-6 10s-6-5-6-10a6 6 0 0 1 6-6z"/><rect x="4" y="22" width="14" height="24"/><rect x="18" y="16" width="14" height="30"/><rect x="32" y="24" width="14" height="22"/><line x1="8" y1="28" x2="14" y2="28"/><line x1="8" y1="34" x2="14" y2="34"/><line x1="22" y1="24" x2="28" y2="24"/><line x1="22" y1="32" x2="28" y2="32"/><line x1="36" y1="30" x2="42" y2="30"/><line x1="36" y1="36" x2="42" y2="36"/></svg>
    <h3>Investment</h3>
    <p>Lorem ipsum dolor sit amet, consectetur adipiscing elit, sed do eiusmod tempor incididunt</p>
  </div>
</section>

<section class="welcome">
  <div class="welcome-bg"></div>
  <div class="welcome-frame"></div>
  <div class="welcome-img" role="img" aria-label="Photo of an investor overlaid with financial charts and data graphics"></div>
  <div class="welcome-text">
    <h2 class="section-title">Welcome To<br><span class="muted">Harlow Ridge Financial<br>Partners</span></h2>
    <div class="rule"></div>
    <p class="serif-copy">Lorem ipsum dolor sit amet, consectetur adipiscing elit, sed do eiusmod tempor incididunt ut labore et dolore magna aliqua. Ut enim ad minim veniam, quis nostrudcitation co laboris nisi ut aliquip ex ea<br>Lorem ipsum dolor sit amet, consectetur adipiscing elit, sed do eiusmod tempor incididunt</p>
  </div>
  <a class="btn welcome-btn">Read More</a>
</section>

<section class="features">
  <div class="band band-left" role="img" aria-label="Photo of colleagues signing documents, tinted navy"></div>
  <div class="band band-right" role="img" aria-label="Photo of a businessman writing on a clipboard, tinted grey"></div>
  <div class="band-block" style="left:89px">
    <h2>Our Company Credentials</h2>
    <div class="rule"></div>
    <p>Lorem ipsum dolor sit amet, consectetur adipiscing elit, sed do eiusmod tempor incididunt ut labore et dolore magna aliqua. Ut enim ad minim veniam, quis nostrud exercitation ullamco laboris nisi ut aliquip ex ea commodo consequat. fugiat nulla pariatur.</p>
  </div>
  <a class="btn band-btn" style="left:91px;background:#8a8a8d">Read More</a>
  <div class="band-block band-right-block" style="left:691px">
    <h2>Our Projects</h2>
    <div class="rule"></div>
    <p>Lorem ipsum dolor sit amet, consectetur ing elit, sed do eiusmod tempor incididunt ut labore et dolore magna aliqua. Ut enim ad minim veniam, quis nostrud exercitation ullamco laboris nisi ut quip ex ea commodo consequat. fugiat nulla</p>
  </div>
  <a class="btn band-btn" style="left:694px">Read More</a>
</section>

<section class="partners">
  <h2 class="partners-title">Our Partners</h2>
  <div class="partners-rule"></div>
  <article class="partner" style="left:119px">
    <div class="partner-photo" role="img" aria-label="Portrait photo of partner Dana Whitfield"></div>
    <h4>Dana Whitfield</h4><span>Lorem ipsum</span>
  </article>
  <article class="partner" style="left:444px">
    <div class="partner-photo" role="img" aria-label="Portrait photo of partner Marcus Orell"></div>
    <h4>Marcus Orell</h4><span>Lorem ipsum</span>
  </article>
  <article class="partner" style="left:770px">
    <div class="partner-photo" role="img" aria-label="Portrait photo of partner Lena Corvale"></div>
    <h4>Lena Corvale</h4><span>Lorem ipsum</span>
  </article>
</section>

<section class="contact">
  <div class="contact-left" role="img" aria-label="Faded photo of a handshake over a desk, tinted grey"></div>
  <div class="contact-right" role="img" aria-label="Photo of a hand with a pen over financial charts, tinted blue"></div>
  <div class="contact-text">
    <h2>Contact Us</h2>
    <div class="rule"></div>
    <p class="serif-copy">Lorem ipsum dolor sit amet, consectetur adipiscing elit, sed do eiusmod tempor incididunt ut labore et dolore magna aliqua. Ut enim ad minim veniam, quis ntion ullco laboris nisi ut aliquip ex ea commodo consequat</p>
    <div class="address">Harlow Ridge Financial Partners<br>14 Alder Crescent<br>48310 55201<br><small>info@harlowridge.example</small></div>
  </div>
  <div class="field" style="top:2978px;height:48px">Name</div>
  <div class="field" style="top:3040px;height:48px">Email</div>
  <div class="field" style="top:3103px;height:100px">Message</div>
  <a class="btn submit">Submit</a>
</section>

<footer>
  <div class="brand footer-brand">
    <div class="brand-mark"></div>
    <div><div class="brand-name">Harlow Ridge</div><div class="brand-sub">Financial Partners</div></div>
  </div>
  <nav class="footer-nav"><a>Home</a><a>About Us</a><a>Projects</a><a>Blog</a></nav>
  <div class="social"><span></span><span></span><span></span><span></span></div>
  <p class="copyright">© 2020 The Company Name. All rights Reserved. Privacy Policy &nbsp;| &nbsp; Terms &amp; Conditions.</p>
</footer>

</body>
</html>
```